BildeVOLD buisnesscard

Hey :) I need a modern buisnesscard for my company BildeVOLD
It most have:
Dagligleder og Fotograf: Henrik Audun Strandvik

Mob: +4700012345
Epost: post@bildevold.example
Adresse: Kvernbakken9, 6040 Bildevik

Facbook and instagram logo with text BildeVOLD

BildeVOLD logo

It Company

```html
<!DOCTYPE html>
<html lang="no">
<head>
<meta charset="utf-8">
<title>BildeVOLD – visittkort</title>
<link rel="stylesheet" href="https://fonts.googleapis.com/css2?family=Montserrat:wght@400;500;700&display=swap">
<style>
  :root {
    --bg: #2b2b2b;
    --card-dark: #000000;
    --card-light: #ffffff;
    --silver: #b1b1b1;
    --silver-edge: #c8c8c8;
    --ink: #111111;
    --ink-soft: #3a3a3a;
    --rule: #8a8a8a;
  }
  * { box-sizing: border-box; margin: 0; padding: 0; }
  html, body {
    width: 1200px; height: 900px; overflow: hidden;
    background: var(--bg);
    font-family: "Montserrat", sans-serif;
  }
  .canvas { position: relative; width: 1200px; height: 900px; }
  .card {
    position: absolute; left: 300px;
    width: 600px; height: 343px;
    border-radius: 22px; overflow: hidden;
  }
  /* Front */
  .card--front { top: 74px; background: var(--card-dark); }
  .card--front .edge-band {
    position: absolute; left: 0; right: 0; bottom: 0; height: 16px;
    background: var(--silver-edge);
    clip-path: polygon(0 40%, 52% 40%, 55% 0, 100% 0, 100% 100%, 0 100%);
  }
  .card--front .brand {
    position: absolute; inset: 0 0 16px 0;
    display: flex; align-items: center; justify-content: center;
    color: var(--silver); font-weight: 700; font-size: 64px; letter-spacing: 0.5px;
  }
  /* Back */
  .card--back { top: 483px; background: var(--card-light); }
  .card--back .edge-band {
    position: absolute; right: 0; bottom: 0; width: 300px; height: 14px;
    background: var(--silver-edge);
    clip-path: polygon(6% 0, 100% 0, 100% 100%, 0 100%);
  }
  .card--back .brand-mark {
    position: absolute; left: 40px; top: 130px; width: 210px;
    text-align: center;
    color: var(--silver); font-weight: 700; font-size: 38px;
  }
  .card--back .divider {
    position: absolute; left: 270px; top: 70px; width: 1.5px; height: 210px;
    background: linear-gradient(to bottom, transparent, var(--rule) 20%, var(--rule) 80%, transparent);
  }
  .contact {
    position: absolute; left: 292px; top: 86px;
    color: var(--ink);
  }
  .contact__name { font-weight: 700; font-size: 21px; }
  .contact__role { font-size: 14px; color: var(--ink-soft); margin-top: 3px; margin-bottom: 14px; }
  .contact__line {
    display: flex; align-items: center; gap: 8px;
    font-size: 14px; line-height: 22px; color: var(--ink);
  }
  .contact__line svg { width: 11px; height: 11px; flex: none; }
  .social {
    position: absolute; right: 34px; top: 236px;
    display: flex; align-items: center; gap: 7px;
    font-size: 14px; color: var(--ink);
  }
  .social__dot { width: 9px; height: 9px; background: var(--ink); }
</style>
</head>
<body>
<div class="canvas">
  <section class="card card--front">
    <div class="brand">BildeVOLD</div>
    <div class="edge-band"></div>
  </section>

  <section class="card card--back">
    <div class="brand-mark">BildeVOLD</div>
    <div class="divider"></div>
    <div class="contact">
      <div class="contact__name">Henrik Audun Strandvik</div>
      <div class="contact__role">Dagligleder og Fotograf</div>
      <div class="contact__line">
        <svg viewBox="0 0 12 12"><path d="M2.5 1 L4.5 1 L5.2 3.5 L4 4.5 Q5 7 7.5 8 L8.5 6.8 L11 7.5 L11 9.5 Q10.5 11 9 11 Q1 10 1 3 Q1 1.5 2.5 1Z" fill="#111"/></svg>
        <span>+4700012345</span>
      </div>
      <div class="contact__line">
        <svg viewBox="0 0 12 12"><rect x="1" y="2.5" width="10" height="7" fill="none" stroke="#111" stroke-width="1.3"/><path d="M1 2.5 L6 6.5 L11 2.5" fill="none" stroke="#111" stroke-width="1.3"/></svg>
        <span>post@bildevold.example</span>
      </div>
      <div class="contact__line">
        <svg viewBox="0 0 12 12"><path d="M6 11.5 Q2 7 2 4.5 A4 4 0 0 1 10 4.5 Q10 7 6 11.5Z" fill="#111"/><circle cx="6" cy="4.5" r="1.5" fill="#fff"/></svg>
        <span>Kvernbakken9, 6040 Bildevik</span>
      </div>
    </div>
    <div class="social">
      <span class="social__dot"></span>
      <span>BildeVOLD</span>
    </div>
    <div class="edge-band"></div>
  </section>
</div>
</body>
</html>
```